Shop front signage design for Bubble Tea Shop

Pearl Hollow is Sydney based Green Tea Shop.We are looking for a modern and sleek signage for shop front end. We have Aluminium Composite Panel and Awning sign at the shop front. We will keep Aluminium composite panel simple with logo and text. We are after awning design which is above glass door and under the panel. Old Awning is PVC foam in two pieces 2310mm w x 1000mm h. We need someone to design awing. It should reflect Bubble tea and using bubble tea cups with pearls is essential. Stock images can be used. Avoid using icons or illustrative icons as we are after real images of bubble tea cup. This is to ensure that the brand is not taken as juice shop or cafe.
Panel Dimensions is 5250 mm w x 580 mm h.Awning/ Fascia sign is 4720 mm w x 1000 mm h.
Logo and signage concept is attached.

Target Market(s)

Corporate Male and Female, school, general public.

Colors
f36e22
333333
000000
eaeaea
cbcbcb

Requirements
Must have
• Bubble tea cups with fruit or milk tea.
Should not have
• Icons, illustration

```html
<!DOCTYPE html>
<html lang="en">
<head>
<meta charset="utf-8">
<title>Pearl Hollow – Awning Sign</title>
<link rel="stylesheet" href="https://fonts.googleapis.com/css2?family=Roboto:wght@400;700;900&display=swap">
<style>
  :root {
    --orange: #f36e22;
    --charcoal: #333333;
    --black: #000000;
    --light-grey: #eaeaea;
    --mid-grey: #cbcbcb;
    --white: #ffffff;
    --page: #f2f2f2;
  }
  html, body {
    margin: 0;
    width: 1200px;
    height: 1000px;
    overflow: hidden;
    background: var(--page);
    font-family: "Roboto", Arial, sans-serif;
  }
  .awning {
    position: absolute;
    left: 57px;
    top: 418px;
    width: 1080px;
    height: 230px;
    background: var(--white);
  }
  .awning-shapes {
    position: absolute;
    inset: 0;
  }
  .cups-photo {
    position: absolute;
    left: 47px;
    top: 15px;
    width: 163px;
    height: 185px;
    border-radius: 10px 10px 22px 22px;
    background: linear-gradient(90deg, #9c79b8 0%, #e9a1b3 50%, #e1d878 100%);
  }
  .brand {
    position: absolute;
    left: 322px;
    top: 96px;
    display: flex;
    align-items: center;
    gap: 18px;
  }
  .brand-dot {
    width: 64px;
    height: 64px;
    border: 7px solid var(--black);
    border-radius: 50%;
    box-sizing: border-box;
  }
  .brand-name {
    font-weight: 700;
    font-size: 50px;
    line-height: 1;
    color: var(--black);
    letter-spacing: -0.5px;
  }
  .menu {
    position: absolute;
    left: 884px;
    top: 50px;
    color: var(--black);
  }
  .menu-label {
    margin: 0 0 4px 14px;
    font-size: 15px;
    font-weight: 400;
    letter-spacing: 0.5px;
    color: var(--charcoal);
  }
  .menu-list {
    list-style: none;
    margin: 0;
    padding: 0;
  }
  .menu-item {
    display: flex;
    align-items: center;
    gap: 6px;
    font-size: 22px;
    font-weight: 700;
    line-height: 28px;
  }
  .menu-item::before {
    content: "";
    width: 8px;
    height: 8px;
    background: var(--orange);
  }
</style>
</head>
<body>
  <section class="awning">
    <svg class="awning-shapes" width="1080" height="230" viewBox="0 0 1080 230" aria-hidden="true">
      <defs>
        <linearGradient id="centre-fade" x1="0" y1="0" x2="0" y2="1">
          <stop offset="0" stop-color="#ffffff"/>
          <stop offset="0.45" stop-color="#eaeaea"/>
          <stop offset="1" stop-color="#cbcbcb"/>
        </linearGradient>
      </defs>
      <polygon points="232,0 850,0 762,230 318,230" fill="url(#centre-fade)"/>
      <g stroke="#000" stroke-width="2">
        <line x1="213" y1="0" x2="301" y2="230"/>
        <line x1="220" y1="0" x2="308" y2="230"/>
        <line x1="227" y1="0" x2="315" y2="230"/>
        <line x1="855" y1="0" x2="765" y2="230"/>
        <line x1="862" y1="0" x2="772" y2="230"/>
        <line x1="869" y1="0" x2="779" y2="230"/>
      </g>
    </svg>

    <div class="cups-photo" role="img" aria-label="Photo of three bubble tea cups with straws: taro, strawberry and mango with tapioca pearls"></div>

    <div class="brand">
      <span class="brand-dot"></span>
      <span class="brand-name">Pearl Hollow</span>
    </div>

    <div class="menu">
      <p class="menu-label">SERVING</p>
      <ul class="menu-list">
        <li class="menu-item">PEARL TEA</li>
        <li class="menu-item">FRUIT TEA</li>
        <li class="menu-item">GREEN TEA</li>
        <li class="menu-item">ICE FRAPPE</li>
      </ul>
    </div>
  </section>
</body>
</html>
```